Wordpress Design Project

Hi,

I would like a more modern colourful design doing for my website ZAP Lnx (www.za%plnx.com - remove percentage). But I do still want to keep the same sort of colors, just maybe lighter. More interesting.

I want the inside pages to NOT all look the same with just boring text.

I want the site to look more appealing and maybe a new logo.
Updates

I would like to mention I would prefer to keep the same logo after rethinking it (possibly a slight refresh of the logo if you feel its a good idea) and the same color scheme as at present.

Saves us rebranding a lot of our apps, tools online ads etc.

Also I thought it is worth mentioning we have 2 parts to the site. The front end and the logged in area. It would be good if when making the front end you keep in mind the back end at http://p.za%plnx.com (remove percentage). We can only edit this limitedly (can edit the entire footer, the logo and full CSS of it). Would be good if we could make sure the header and footer can be used on the back end as well maybe to make it match.

I also want layouts making not just for the homepage. Obviously every page will basically be the same but I don't want all the other pages to just be 'text' and no real layout.

You can see out main pages on the website at the moment, I want those other pages to be laid out nice and differently as well. For example the testimonials page could be more interesting with speech bubbles and pictures of each person (just use placeholders). The affiliates page could be a description and then a nice fancy list of features why to join etc. 

Nothing overly complicated but I think it makes the whole site seem a lot better.

Target Market(s)

Affiliate Marketing. International.

Requirements
Must have
• Needs to be more room for links across the navigation at the top, also sub menus (at present we have a lot of pages which are hidden deep within other pages).
Nice to have
• Lists of features for advertisers and affiliates on the homepage part.

Menu items and buttons have nice hover over effects.

I want to get across on our pages all the different unique features we have.

Maybe some kind of slider which has past offer logos in, just use example logos.

```html
<!DOCTYPE html>
<html lang="en">
<head>
<meta charset="utf-8">
<title>ZAP Lnx – International Affiliate Network</title>
<link href="https://fonts.googleapis.com/css2?family=Signika:wght@400;600&family=Open+Sans:wght@400;600&display=swap" rel="stylesheet">
<style>
:root{
  --orange:#f7941d;
  --orange-dark:#e97d0c;
  --blue:#0a4f96;
  --blue-dark:#083f7d;
  --blue-head:#0d4d8f;
  --sky:#6cc0f2;
  --yellow:#fcc72c;
  --pale:#ecf3f3;
  --grey-text:#7a7a7a;
  --body-text:#555;
  --panel:#f1f1f1;
}
*{margin:0;padding:0;box-sizing:border-box}
html,body{width:893px;height:1200px;overflow:hidden;background:#fff}
body{position:relative;font-family:"Open Sans",Arial,sans-serif;color:var(--body-text)}
.abs{position:absolute}
.head-font{font-family:"Signika",Arial,sans-serif}

/* header */
.brand{left:127px;top:12px;display:flex;align-items:center;gap:8px}
.brand-mark{width:14px;height:14px;background:var(--orange)}
.brand-name{font-family:"Signika",Arial,sans-serif;font-weight:600;font-size:42px;color:var(--orange);line-height:1}
.top-btn{top:12px;height:23px;border-radius:4px;background:var(--orange-dark);color:#fff;font-family:"Signika",sans-serif;font-size:12px;display:flex;align-items:center;justify-content:center}
.phone{right:112px;top:45px;font-family:"Signika",sans-serif;font-weight:600;font-size:19px;color:#111}

.main-nav{left:0;top:77px;width:893px;height:27px;background:linear-gradient(#fba33b,var(--orange-dark))}
.main-nav ul{list-style:none;display:flex;margin-left:131px;height:100%}
.main-nav li{font-family:"Signika",sans-serif;font-size:14.5px;color:#fff;padding:0 13px;display:flex;align-items:center}
.main-nav li.active{background:var(--blue);padding:0 6px;margin-right:7px}

/* hero */
.hero{left:0;top:104px;width:893px;height:392px;background:radial-gradient(ellipse at 60% 40%,#1566b1,var(--blue) 60%,var(--blue-dark))}
.hero-rule{left:112px;top:130px;width:669px;height:1px;background:rgba(255,255,255,.2)}
.hero-kicker{left:0;width:893px;top:121px;text-align:center;font-family:"Signika",sans-serif;font-weight:600;font-size:19px;color:var(--sky);letter-spacing:.5px}
.hero-title{left:0;width:893px;top:146px;text-align:center;font-family:"Signika",sans-serif;font-weight:600;font-size:33px;color:#fff}
.hero-art{left:130px;top:138px;width:610px;height:325px;border-radius:6px;background:linear-gradient(100deg,rgba(110,180,235,.55),rgba(40,110,180,.35) 45%,rgba(235,240,248,.45))}
.join-cta{left:515px;top:441px}

/* intro strip */
.intro{left:0;top:496px;width:893px;height:156px;background:var(--pale)}
.intro-col{top:506px;width:325px}
.intro-col h2{font-family:"Signika",sans-serif;font-weight:600;font-size:21px;color:var(--orange);margin-bottom:6px}
.intro-col p{font-size:11px;line-height:16px;color:var(--body-text)}
.signup-btn{position:absolute;top:93px;left:0;width:129px;height:32px;border-radius:5px;background:linear-gradient(#ffd64d,#f9b914);box-shadow:0 2px 0 #d99a0b;font-family:"Signika",sans-serif;font-weight:600;font-size:17px;color:#333;display:flex;align-items:center;justify-content:center}
.dots{left:0;width:893px;height:8px;background-image:radial-gradient(#cfdcdc 1px,transparent 1.3px);background-size:4px 4px}

/* login */
.login-box{left:112px;top:673px;width:158px;height:184px;background:var(--panel);border-radius:4px;padding:12px 14px}
.login-box h3{font-family:"Signika",sans-serif;font-weight:400;font-size:15px;color:#111;margin-bottom:9px}
.field{height:29px;background:#fff;border-radius:5px;font-size:11px;color:#222;padding:7px 8px;margin-bottom:14px}
.forgot{font-size:9.5px;color:#222;margin-top:-4px}
.login-row{display:flex;align-items:center;gap:6px;margin-top:10px;font-size:9.5px;color:#222}
.login-btn{width:48px;height:22px;border:1px solid #aaa;border-radius:5px;background:linear-gradient(#fff,#ddd);font-size:11px;font-weight:600;display:flex;align-items:center;justify-content:center}

/* welcome */
.welcome{left:299px;top:671px;width:483px}
.welcome h1{font-family:"Signika",sans-serif;font-weight:600;font-size:22px;color:var(--blue-head);margin-bottom:9px}
.welcome p{font-size:10px;line-height:14.5px;color:var(--grey-text);margin-bottom:7px}

/* sidebar */
.side-title{font-family:"Signika",sans-serif;font-size:15px;color:var(--blue-head);font-weight:600}
.post-list{left:112px;top:904px;width:158px;list-style:none;border-bottom:2px solid #ddd}
.post-list li{font-size:10px;color:var(--grey-text);height:21px;line-height:20px;border-bottom:1px solid #eee;padding-left:9px;position:relative}
.post-list li:last-child{border-bottom:none}
.post-list li::before{content:"›";position:absolute;left:0;color:#aaa}
.social{left:113px;top:1017px;display:flex;gap:12px}
.social span{width:30px;height:30px;border-radius:4px}

/* why join */
.why{left:299px;top:884px;width:227px;height:166px;background:var(--orange);border-radius:5px;padding:10px 14px}
.why h3{font-family:"Signika",sans-serif;font-weight:600;font-size:15px;color:#fff;margin-bottom:8px}
.why ul{list-style:none}
.why li{font-size:10px;color:#fff;line-height:13px;margin-bottom:4.5px;padding-left:6px;position:relative}
.why li::before{content:"›";position:absolute;left:0}

/* testimonial */
.testimonial{left:556px;top:890px;width:226px}
.testimonial h3{font-family:"Signika",sans-serif;font-weight:600;font-size:15.5px;color:var(--blue-head);margin-bottom:9px}
.testimonial blockquote{font-size:10px;line-height:16px;color:var(--body-text);padding-bottom:10px}
.quote-line{left:556px;top:1039px}
.quote-by{right:112px;top:1050px;font-size:10px;color:#222}

/* badges */
.badge{top:1093px;width:100px;height:29px;border:1px solid #cfd8e0;background:#f6f8fa;display:flex;align-items:center;gap:5px;padding:0 5px}
.badge i{width:18px;height:18px;border-radius:50%;flex:none}
.badge b{display:block;font-size:7.5px;color:var(--blue-head);font-weight:600;line-height:9px}
.badge small{display:block;font-size:4.5px;color:#666;line-height:6px}

/* footer */
.footer{left:0;top:1145px;width:893px;height:55px;background:var(--pale)}
.footer-links{left:0;width:893px;top:1155px;display:flex;justify-content:center;gap:20px;font-size:9.5px;color:#333}
.footer-links .sep{color:#555}
.copyright{left:0;width:893px;top:1177px;text-align:center;font-size:9.5px;color:#666}
</style>
</head>
<body>

<header>
  <div class="abs brand"><span class="brand-mark"></span><span class="brand-name">ZAP Lnx</span></div>
  <div class="abs top-btn" style="left:668px;width:50px">LOGIN</div>
  <div class="abs top-btn" style="left:727px;width:54px">SING UP</div>
  <div class="abs phone">+44 (0)1632 960418</div>
</header>

<nav class="abs main-nav">
  <ul>
    <li class="active">HOME</li><li>ABOUT US</li><li>OUR BLOG</li><li>TESTIMONIALS</li><li>AFFILIATES</li><li>ADVERTISERS</li><li>CONTACT US</li>
  </ul>
</nav>

<section class="abs hero" aria-label="Hero"></section>
<div class="abs hero-art" role="img" aria-label="Illustration: large blue dollar sign with a figure placing a puzzle piece, dashboard screenshots over a faint world map"></div>
<div class="abs hero-rule"></div>
<div class="abs hero-kicker">INTERNATIONAL</div>
<div class="abs hero-title">AFFILIATE NETWORK</div>
<svg class="abs join-cta" width="134" height="40" viewBox="0 0 134 40">
  <polygon points="0,4 112,4 112,0 134,20 112,40 112,36 0,36 10,20" fill="#fcc72c"/>
  <text x="66" y="25" text-anchor="middle" font-family="Signika, sans-serif" font-weight="600" font-size="14" fill="#222">JOIN US TODAY!</text>
</svg>

<section class="abs intro"></section>
<div class="abs intro-col" style="left:112px">
  <h2>AFFILIATES</h2>
  <p>Get access to a wide range of top performing offers for your websites and email marketing lists. Fresh and exclusive offers to promote. Join over 2,000 affiliates already signed up to ZAP Lnx.</p>
  <div class="signup-btn">SIGN UP NOW</div>
</div>
<div class="abs intro-col" style="left:460px">
  <h2>ADVERTISERS</h2>
  <p>Generate sales/leads to your website instantly with the ZAP Lnx Affiliate Network. Only pay on performance, no monthly or setup fees. ZAP Lnx takes the risk out of advertising.</p>
  <div class="signup-btn">SIGN UP NOW</div>
</div>
<div class="abs dots" style="top:648px"></div>

<aside class="abs login-box">
  <h3>ACCOUNT LOGIN</h3>
  <div class="field">Email</div>
  <div class="field">Password</div>
  <div class="forgot">Forgot Password</div>
  <div class="login-row"><span class="login-btn">LOGIN</span>or Sign Up</div>
</aside>

<article class="abs welcome">
  <h1>WELCOME TO ZAP LNX</h1>
  <p>Welcome to the ZAP Lnx affiliate network. On time payments, hot &amp; exclusive CPL/CPA offers, fast support and low fees for advertisers, is the making of a leading affiliate network!</p>
  <p>ZAP Lnx offer a wide range of advertisers for your websites. So you can start monetizing your traffic or get an additional revenue stream, today.</p>
  <p>With the ZAP Lnx Affiliate Network we focus on lead generation offers. We have a range of competitions, surveys, incentives and gambling offers. Whatever the industry, you will be able to find offers to suit your traffic.</p>
  <p>ZAP Lnx is a powerful performance-based internet marketing network dedicated to advertisers to affiliates through its powerful affiliate network.</p>
</article>

<div class="abs side-title" style="left:112px;top:880px">RECENT BLOG POSTS</div>
<ul class="abs post-list">
  <li>New Offers For China</li><li>NEW: Banner Rotators</li><li>New Offers</li>
</ul>
<div class="abs side-title" style="left:112px;top:991px">SOCIAL NETWORKING</div>
<div class="abs social">
  <span style="background:#3b5a98"></span><span style="background:#5fc3ea"></span><span style="background:#c9241d"></span><span style="background:#1f6ea6"></span>
</div>

<section class="abs why">
  <h3>WHY JOIN ZAP LNX?</h3>
  <ul>
    <li>High Payouts</li><li>Reliable Tracking</li><li>Great Affiliate Support</li><li>Exclusive Offers</li>
    <li>Monthly/Bi-monthly/Weekly Payments (more info)</li><li>View Stats on Your Mobile</li>
  </ul>
</section>

<section class="abs testimonial">
  <h3>TESTIMONIALS</h3>
  <blockquote>"I decided to start using ZAP Lnx after using several other ZAP sites. I was impressed with the customer service and support provided in comparison to some other networks I have used. ZAP Lnx also has a large range of offers, retailers so is the perfect solution to earning commission. Payments are always on-time too."</blockquote>
</section>
<svg class="abs quote-line" width="226" height="10" viewBox="0 0 226 10">
  <polyline points="0,1 176,1 190,9 190,1 226,1" fill="none" stroke="#bbb" stroke-width="1"/>
</svg>
<div class="abs quote-by">Rory Dalton – Sitebay</div>

<div class="abs badge" style="left:222px"><i style="background:#1d3f6e;border-radius:3px"></i><span><b>Mobile Stats</b><small>ZAP Lnx Mobile Website</small></span></div>
<div class="abs badge" style="left:338px"><i style="background:#e8751a"></i><span><b>Ember Browser</b><small>Official ZAP Lnx Extension</small></span></div>
<div class="abs badge" style="left:454px"><i style="background:#3a8de0"></i><span><b>Orbit Browser</b><small>Official ZAP Lnx Extension</small></span></div>
<div class="abs badge" style="left:570px"><i style="background:#8cbf26;border-radius:3px"></i><span><b>Phone App</b><small>Official ZAP Lnx App</small></span></div>

<div class="abs dots" style="top:1137px"></div>
<footer class="abs footer"></footer>
<div class="abs footer-links">
  <span>Affiliate Terms &amp; Conditions</span><span class="sep">|</span><span>Advertiser Terms &amp; Conditions</span><span class="sep">|</span><span>Privacy Policy &amp; Cookies</span><span class="sep">|</span><span>FAQ</span><span class="sep">|</span><span>Contact Us</span>
</div>
<div class="abs copyright">© 2013 ZAP Media UK Ltd - All Rights Reserved.</div>

</body>
</html>
```